Wordpress theme website for professionals working together

My partner and I are offering business services, my wife in the energy business as mainly as member of the board of commissioners. I am working as interim manager/consultant in the accounting and finance area. Both activities are connected in one company VELMOT BV (dutch ltd). We need a CV based website. Beside this we do some financial and accounting services.

Target Market(s)

small medium business

Font styles to use
Sans Serif

Colors

Designer to choose colors to be used in the design.

Requirements
Must have
• Pictures of both members.
• CLEAN AND SIMPLE
• I LIKE BLACK & WHITE
Nice to have
• I like design like this theme: http://theme.pruxelo-example.com/resume/

```html
<!DOCTYPE html>
<html lang="en">
<head>
<meta charset="utf-8">
<title>VELMOT BV – Who are we?</title>
<link rel="stylesheet" href="https://fonts.googleapis.com/css2?family=Montserrat:wght@400;500;600&family=Open+Sans:wght@400&display=swap">
<style>
:root{
  --navy:#12306b;
  --red:#c8090f;
  --ink:#222;
  --nav-grey:#6b6b6b;
  --white:#ffffff;
  --black:#000000;
  --footer-text:#b9b9b9;
  --field:#f3f5fa;
  --rule:#2e2e2e;
}
*{margin:0;padding:0;box-sizing:border-box}
html,body{width:1200px;height:907px;overflow:hidden;background:var(--white)}
body{position:relative;font-family:"Open Sans",sans-serif}
.site-header{position:absolute;left:0;top:0;width:1200px;height:65px;background:var(--white)}
.brand{position:absolute;left:172px;top:18px;display:flex;align-items:center;gap:8px;font-family:"Montserrat",sans-serif;font-weight:600;font-size:30px;color:var(--navy);letter-spacing:-0.5px;line-height:1}
.brand-mark{width:10px;height:10px;background:var(--red)}
.main-nav{position:absolute;right:173px;top:28px;display:flex;gap:29px;font-family:"Montserrat",sans-serif;font-size:11.5px;font-weight:500;letter-spacing:1px;color:var(--nav-grey)}
.main-nav .active{color:var(--ink);font-weight:600}
.hero{position:absolute;left:0;top:65px;width:1200px;height:554px;background:linear-gradient(100deg,#121820 0%,#1c2027 35%,#2a2220 65%,#1f1f22 100%)}
.hero-title{position:absolute;left:0;top:92px;width:100%;text-align:center;font-family:"Montserrat",sans-serif;font-weight:600;font-size:51px;letter-spacing:5px;color:var(--white)}
.member{position:absolute;top:186px;width:238px;text-align:center}
.member-frame{width:238px;height:238px;border-radius:50%;border:2.5px solid var(--white);padding:8px;background:#1b1b1d}
.member-photo{width:100%;height:100%;border-radius:50%}
.member-name{margin-top:18px;font-family:"Montserrat",sans-serif;font-weight:500;font-size:22px;letter-spacing:0.5px;color:var(--white)}
.member--henk{left:342px}
.member--henk .member-photo{background:radial-gradient(circle at 50% 45%,#b99a88 0%,#8c7a70 45%,#cfcfcf 80%)}
.member--marja{left:620px}
.member--marja .member-photo{background:radial-gradient(circle at 50% 45%,#c9a59a 0%,#8f7875 45%,#9aa3b0 80%)}
.slider-arrow{position:absolute;top:270px}
.slider-arrow--prev{left:59px}
.slider-arrow--next{left:1105px}
.site-footer{position:absolute;left:0;top:619px;width:1200px;height:288px;background:var(--black);color:var(--white)}
.footer-col{position:absolute;top:34px}
.footer-col h3{font-family:"Montserrat",sans-serif;font-weight:500;font-size:20px;color:var(--white);margin-bottom:16px}
.footer-col ul{list-style:none}
.footer-col li{font-size:10.5px;line-height:20.25px;color:var(--footer-text)}
.col-company{left:172px}.col-about{left:352px}.col-links{left:517px}.col-news{left:708px}
.signup{display:flex;width:320px;height:33px;margin-top:1px}
.signup-field{flex:1;background:var(--field);border-radius:17px 0 0 17px;font-size:10px;color:#888;padding:9px 11px}
.signup-btn{width:85px;background:var(--red);border-radius:0 17px 17px 0;color:var(--white);font-family:"Montserrat",sans-serif;font-weight:600;font-size:12px;display:flex;align-items:center;justify-content:center}
.social{display:flex;gap:31px;margin-top:30px;padding-left:3px}
.social span{width:17px;height:17px;background:var(--white);border-radius:3px}
.footer-rule{position:absolute;left:172px;top:228px;width:856px;height:1px;background:var(--rule)}
.copyright{position:absolute;left:0;top:252px;width:100%;text-align:center;font-size:12px;color:var(--white)}
</style>
</head>
<body>
<header class="site-header">
  <div class="brand"><span>VELMOT</span><span class="brand-mark"></span></div>
  <nav class="main-nav">
    <span class="active">HOME</span><span>MARJA</span><span>SKILLS</span><span>EXPERIENCE</span><span>PORTFOLIO</span><span>EDUCATION</span><span>CONTACT</span>
  </nav>
</header>

<section class="hero" role="img" aria-label="Dimmed photograph of a brick office building at dusk">
  <h1 class="hero-title">WHO ARE WE?</h1>
  <svg class="slider-arrow slider-arrow--prev" width="36" height="74" viewBox="0 0 36 74"><polyline points="34,1 1,37 34,73" fill="none" stroke="#bbb" stroke-width="1.2"/></svg>
  <svg class="slider-arrow slider-arrow--next" width="36" height="74" viewBox="0 0 36 74"><polyline points="2,1 35,37 2,73" fill="none" stroke="#bbb" stroke-width="1.2"/></svg>
  <div class="member member--henk">
    <div class="member-frame"><div class="member-photo" role="img" aria-label="Portrait photo of Henk Dorsman"></div></div>
    <p class="member-name">HENK DORSMAN</p>
  </div>
  <div class="member member--marja">
    <div class="member-frame"><div class="member-photo" role="img" aria-label="Portrait photo of Marja Veldkamp"></div></div>
    <p class="member-name">MARJA VELDKAMP</p>
  </div>
</section>

<footer class="site-footer">
  <div class="footer-col col-company"><h3>Company</h3><ul><li>Sed ut perspiciatis</li><li>Unde omnis iste</li><li>Voluptatem</li><li>Accusantium</li><li>Doloremque</li><li>Laudantium</li></ul></div>
  <div class="footer-col col-about"><h3>About</h3><ul><li>Sed ut perspiciatis</li><li>Unde omnis iste</li><li>Voluptatem</li><li>Accusantium</li><li>Doloremque</li><li>Laudantium</li></ul></div>
  <div class="footer-col col-links"><h3>Links</h3><ul><li>Sed ut perspiciatis</li><li>Unde omnis iste</li><li>Voluptatem</li><li>Accusantium</li><li>Doloremque</li><li>Laudantium</li></ul></div>
  <div class="footer-col col-news"><h3>Newsletter</h3>
    <div class="signup"><div class="signup-field">Email:</div><div class="signup-btn">SIGN UP</div></div>
    <div class="social"><span></span><span></span><span></span><span></span></div>
  </div>
  <div class="footer-rule"></div>
  <p class="copyright">© 2018 All Rights Are Reserved.Terms of Use | Privacy Policy</p>
</footer>
</body>
</html>
```